In need of an AWESOME website for our Water Re-filling Store

The project is to design a website for our retail store front with the website www.quellbrookfillhouse.com. Currently if you go to that site it redirects you to our other site www.quellbrookbottleworks.com which is just our water bottle website. So, I need a new website created for www.quellbrookfillhouse.com (retail storefront)
Use our Squarespace to create a site with pages to help educate, tell about us, link to our water bottle brand site that is already created with Squarespace, and show the family and community aspects that we believe in. Our current water bottle website is www.quellbrookbottleworks.com for reference
We also sell hydration products, especially PRZQ products and have access to digital media through our PRZQ dealer site. we sell bottles, dispensers and other supplies for water refilling customers. We sell Ice as well.

Target Market(s)

Local residents looking to fill up their 1-5 gallon water jugs

Industry/Entity Type

Alkaline and Purified Water Retail Re-filling Store

Coding

Coded - Design and coding required

Font styles to use
Serif
Sans Serif

Colors
0054AA
0677BA
7BADD7
CADEEF
E8F1F8

Requirements
Must have
• pictures of our family in the about us section and pictures of our store inside and out.

```html
<!DOCTYPE html>
<html lang="en">
<head>
<meta charset="utf-8">
<title>Quellbrook Fill House</title>
<link rel="stylesheet" href="https://fonts.googleapis.com/css2?family=Montserrat:wght@600;700&family=Lato:wght@400;700&display=swap">
<style>
:root{
  --blue:#0054AA;
  --blue-mid:#0677BA;
  --blue-soft:#7BADD7;
  --blue-pale:#CADEEF;
  --blue-mist:#E8F1F8;
  --navy:#1e2466;
  --heading:#23286e;
  --ink:#3a3a3a;
  --footer:#232323;
  --white:#fff;
}
*{margin:0;padding:0;box-sizing:border-box}
html,body{width:1200px;height:3850px;overflow:hidden;background:var(--white)}
body{position:relative;font-family:"Lato",sans-serif;color:var(--ink)}
.abs{position:absolute}
.heading{font-family:"Montserrat",sans-serif;font-weight:700;color:var(--heading);text-transform:uppercase;letter-spacing:.5px}
.btn{position:absolute;display:flex;align-items:center;justify-content:center;background:var(--navy);color:var(--white);border-radius:22px;font-size:15px}
.rule{position:absolute;height:3px;background:var(--blue)}
.photo{position:absolute;border-radius:8px}

/* header */
.brand{left:110px;top:38px;font-weight:700;font-size:24px;color:var(--blue-mid);display:flex;align-items:center;gap:10px}
.brand-dot{width:22px;height:22px;border-radius:50%;background:var(--blue)}
.phone-badge{left:681px;top:15px;width:48px;height:48px;border-radius:50%;background:var(--blue);display:flex;align-items:center;justify-content:center}
.phone-num{left:744px;top:26px;font-size:20px;color:var(--navy)}
.nav{top:81px;font-size:16px;color:#555}
.nav.active{color:var(--blue-mid);font-weight:700}

/* hero */
.hero-left{left:0;top:120px;width:597px;height:557px;background:linear-gradient(180deg,#0a6cc6 0%,#0058b0 60%,#1e78c8 85%,#0057ad 100%)}
.hero-title{left:108px;top:218px;font-size:49px;line-height:58px;color:var(--white)}
.hero-text{left:112px;top:358px;width:420px;font-size:22px;line-height:31px;color:var(--white);text-align:justify}

/* sections */
.center{left:0;width:1200px;text-align:center}
.section-title{font-size:39px}
.lead{font-size:16px;line-height:25px;color:#444}
.card-label{font-family:"Montserrat",sans-serif;font-weight:600;font-size:23px;color:var(--blue-mid);width:302px;text-align:center}
.arrow{position:absolute;width:30px;height:30px;border-radius:50%;background:var(--navy);display:flex;align-items:center;justify-content:center}
.about-text{left:676px;width:413px;font-size:16px;line-height:25px;text-align:justify;color:#444}

.cta{left:0;top:1945px;width:1200px;height:412px;background:linear-gradient(180deg,#0a64bd 0%,#0057ad 45%,#2a82cc 60%,#0056ab 100%)}

/* footer */
.footer{left:0;top:3406px;width:1200px;height:444px;background:var(--footer)}
.f-brand{left:110px;top:3568px;width:250px;display:flex;align-items:center;justify-content:center;gap:8px;font-weight:700;font-size:22px;color:var(--blue-mid)}
.f-head{font-family:"Montserrat",sans-serif;font-weight:600;font-size:20px;color:var(--white)}
.f-link{font-size:15px;color:var(--white)}
.social{position:absolute;top:3695px;width:22px;height:22px;border-radius:50%;border:2px solid var(--white)}
.social.active{border:none;border-radius:4px;background:var(--blue-mid);width:26px;height:26px;top:3693px}
</style>
</head>
<body>

<!-- header -->
<div class="abs brand"><span class="brand-dot"></span>Quellbrook Fill House</div>
<div class="abs phone-badge">
  <svg width="24" height="24" viewBox="0 0 24 24"><path d="M6.6 10.8c1.4 2.8 3.8 5.1 6.6 6.6l2.2-2.2c.3-.3.7-.4 1-.2 1.1.4 2.3.6 3.6.6.6 0 1 .4 1 1V20c0 .6-.4 1-1 1C10.6 21 3 13.4 3 4c0-.6.4-1 1-1h3.5c.6 0 1 .4 1 1 0 1.3.2 2.5.6 3.6.1.3 0 .7-.2 1L6.6 10.8z" fill="#fff"/></svg>
</div>
<div class="abs phone-num">(520) 555-0148</div>
<div class="btn" style="left:920px;top:18px;width:165px;height:42px">View Products</div>
<div class="abs nav active" style="left:462px">Home</div>
<div class="abs nav" style="left:552px">About Us</div>
<div class="abs nav" style="left:665px">Products</div>
<div class="abs nav" style="left:776px">Gallery</div>
<div class="abs nav" style="left:874px">Community</div>
<div class="abs nav" style="left:1005px">Contact Us</div>

<!-- hero -->
<div class="abs hero-left"></div>
<h1 class="abs heading hero-title" style="color:var(--white)">Your Local<br>Hydration Hub</h1>
<p class="abs hero-text">A locally owned hydration spot dedicated to helping families stay healthy, energized, and connected.</p>
<div class="btn" style="left:112px;top:489px;width:165px;height:42px">Visit Our Store</div>
<div class="abs" role="img" aria-label="Storefront exterior with store sign above glass entrance doors" style="left:600px;top:120px;width:600px;height:557px;background:linear-gradient(180deg,#a8a08e 0%,#8d8676 45%,#3a3a3c 70%,#6b675e 100%)"></div>

<!-- products -->
<h2 class="abs heading section-title center" style="top:780px">Our Products</h2>
<div class="rule" style="left:550px;top:836px;width:100px"></div>
<p class="abs lead center" style="top:855px">From everyday essentials to performance hydration, we carry the products you need to<br>stay refreshed, energized, and ready for anything.</p>
<div class="arrow" style="left:63px;top:1049px"><svg width="12" height="12" viewBox="0 0 12 12"><path d="M8 1 3 6l5 5" stroke="#fff" stroke-width="2" fill="none"/></svg></div>
<div class="arrow" style="left:1106px;top:1049px"><svg width="12" height="12" viewBox="0 0 12 12"><path d="M4 1l5 5-5 5" stroke="#fff" stroke-width="2" fill="none"/></svg></div>
<div class="photo" role="img" aria-label="Cooler stocked with PRZQ drink cans" style="left:111px;top:929px;width:302px;height:267px;background:linear-gradient(180deg,#2b2b30,#8a7b86 50%,#3a3a40)"></div>
<div class="photo" role="img" aria-label="Two staff members with water jugs in front of the refill room" style="left:449px;top:929px;width:302px;height:267px;background:linear-gradient(135deg,#3e66b8,#8a8c92 55%,#2f3a55)"></div>
<div class="photo" role="img" aria-label="Freezer filled with bagged ice" style="left:787px;top:929px;width:302px;height:267px;background:linear-gradient(180deg,#cfd6e0,#eef1f6 50%,#b9c2ce)"></div>
<div class="abs card-label" style="left:111px;top:1210px">PRZQ Products</div>
<div class="abs card-label" style="left:449px;top:1210px">Water Refills</div>
<div class="abs card-label" style="left:787px;top:1210px">Ice Sales</div>

<!-- about -->
<div class="photo" role="img" aria-label="Family portrait on the beach" style="left:111px;top:1375px;width:456px;height:439px;background:linear-gradient(180deg,#c9cccb 0%,#b4b7b4 35%,#9a9c97 70%,#b9bab5 100%)"></div>
<h2 class="abs heading section-title" style="left:676px;top:1385px">About Us</h2>
<div class="rule" style="left:676px;top:1440px;width:107px"></div>
<p class="abs about-text" style="top:1470px">Quellbrook Fill House was created with a simple goal—to provide clean, reliable hydration options for our community while building something meaningful for our family.</p>
<p class="abs about-text" style="top:1594px">What started as an idea quickly became a place where people could come not just for water, but for convenience, quality, and connection. We saw the need for a better, more accessible way to stay hydrated and made it our mission to deliver exactly that.</p>
<div class="btn" style="left:676px;top:1751px;width:131px;height:42px">Read More</div>

<!-- call to action -->
<div class="abs cta"></div>
<h2 class="abs heading center" style="top:2032px;font-size:40px;color:var(--white)">Come In. Refill. Feel the Difference.</h2>
<p class="abs center" style="top:2108px;font-size:22px;line-height:30px;color:var(--white)">Stop by today for clean water, premium hydration products, and<br>a friendly, local experience.</p>
<div class="btn" style="left:518px;top:2217px;width:165px;height:42px">Visit Our Store</div>

<!-- gallery -->
<h2 class="abs heading section-title center" style="top:2478px">Our Gallery</h2>
<div class="rule" style="left:548px;top:2534px;width:104px"></div>
<p class="abs lead center" style="top:2553px">From our store to our family—take a look at the people, place, and experience<br>behind Quellbrook Fill House.</p>
<div class="photo" role="img" aria-label="Technician installing filtration equipment" style="left:111px;top:2627px;width:306px;height:420px;background:linear-gradient(160deg,#c8ccd2,#8b8f96 50%,#4a5d7a)"></div>
<div class="photo" role="img" aria-label="Stainless steel alkaline and purified refill stations" style="left:447px;top:2627px;width:304px;height:193px;background:linear-gradient(180deg,#c4c7cb,#9ea2a7)"></div>
<div class="photo" role="img" aria-label="Store interior with blue wall and refill counter" style="left:782px;top:2627px;width:307px;height:193px;background:linear-gradient(180deg,#e6e7ea,#3c63b3 50%,#9a9ca2)"></div>
<div class="photo" role="img" aria-label="Wall display of bottles and water jugs" style="left:445px;top:2857px;width:306px;height:192px;background:linear-gradient(180deg,#e9ebee,#2a2c33 50%,#a8c0dc)"></div>
<div class="photo" role="img" aria-label="Sign installation on the storefront with a lift truck" style="left:782px;top:2853px;width:307px;height:421px;background:linear-gradient(180deg,#b4a896,#8e826e 55%,#5e5a55)"></div>
<div class="photo" role="img" aria-label="Blue filter housings in the treatment room" style="left:111px;top:3081px;width:306px;height:192px;background:linear-gradient(90deg,#d7d9dc,#2d5fa8 50%,#e5e6e8)"></div>
<div class="photo" role="img" aria-label="Front entrance of the store" style="left:445px;top:3081px;width:306px;height:192px;background:linear-gradient(180deg,#a59c8a,#3b3b3d 60%,#8e8a82)"></div>

<!-- footer -->
<div class="abs footer"></div>
<div class="abs f-brand"><span style="width:18px;height:18px;border-radius:50%;background:var(--blue-mid)"></span>Quellbrook Fill House</div>
<div class="abs" style="left:110px;top:3652px;width:250px;text-align:center;font-size:15px;color:var(--white)">Stay refreshed. Stay connected.</div>
<a class="social active" style="left:168px" aria-label="Social profile"></a>
<a class="social" style="left:212px" aria-label="Social profile"></a>
<a class="social" style="left:245px" aria-label="Social profile"></a>
<a class="social" style="left:280px" aria-label="Social profile"></a>

<div class="abs f-head" style="left:454px;top:3496px">Main Links</div>
<div class="abs f-link" style="left:454px;top:3558px">Home</div>
<div class="abs f-link" style="left:454px;top:3606px">About Us</div>
<div class="abs f-link" style="left:454px;top:3653px">Products</div>
<div class="abs f-link" style="left:454px;top:3700px">Contact Us</div>

<div class="abs f-head" style="left:642px;top:3496px">Other Links</div>
<div class="abs f-link" style="left:642px;top:3558px">Privacy Policy</div>
<div class="abs f-link" style="left:642px;top:3606px">Terms &amp; Conditions</div>
<div class="abs f-link" style="left:642px;top:3653px">Disclaimer</div>
<div class="abs f-link" style="left:642px;top:3700px">Accessibility</div>

<div class="abs f-head" style="left:858px;top:3496px">Address</div>
<svg class="abs" style="left:856px;top:3564px" width="18" height="18" viewBox="0 0 24 24"><path d="M6.6 10.8c1.4 2.8 3.8 5.1 6.6 6.6l2.2-2.2c.3-.3.7-.4 1-.2 1.1.4 2.3.6 3.6.6.6 0 1 .4 1 1V20c0 .6-.4 1-1 1C10.6 21 3 13.4 3 4c0-.6.4-1 1-1h3.5c.6 0 1 .4 1 1 0 1.3.2 2.5.6 3.6.1.3 0 .7-.2 1L6.6 10.8z" fill="var(--blue-mid)"/></svg>
<div class="abs f-link" style="left:889px;top:3563px">(520) 555-0148</div>
<svg class="abs" style="left:856px;top:3625px" width="18" height="14" viewBox="0 0 18 14"><rect width="18" height="14" rx="2" fill="var(--blue-mid)"/><path d="M1 2l8 6 8-6" stroke="#232323" stroke-width="1.5" fill="none"/></svg>
<div class="abs f-link" style="left:889px;top:3622px">sales@quellbrookfillhouse.com</div>
<svg class="abs" style="left:856px;top:3682px" width="14" height="20" viewBox="0 0 14 20"><path d="M7 0C3.1 0 0 3.1 0 7c0 5 7 13 7 13s7-8 7-13c0-3.9-3.1-7-7-7zm0 9.5A2.5 2.5 0 1 1 7 4.5a2.5 2.5 0 0 1 0 5z" fill="var(--blue-mid)"/></svg>
<div class="abs f-link" style="left:889px;top:3682px;line-height:20px">4820 W. Juniper Ridge Rd., Ste.<br>12 Marana, AZ 85658</div>

<div class="abs" style="left:110px;top:3802px;width:979px;height:1px;background:#444"></div>
<div class="abs" style="left:0;top:3822px;width:1200px;text-align:center;font-size:13px;color:var(--white)">Copyright © 2026 Quellbrook Fill House. All rights reserved.</div>
</body>
</html>
```